Business Card Design Project

We are not a new company, but renamed to "Vantorin Kitchens" last year. We specialize in modern high-end cabinetry imports. We would like to communicate a sense of quality and cutting edge technology. Ideally the design would incorporate our logo colors, silver, red and preferably a black, matte background. Though we are open to suggestions.
Logo is attached.
Edit: I have attached rough drafts of the previous cards, this way you will have all necessary content that needs to go on the cards.
Updates
Project Deadline Extended
Reason: We have received a lot of great designs, but due to the sheer number we couldn't respond to all. We will extend the deadline for another 7 days to finalize and provide feedback to designers.
Thank you for your hard work!
Industry/Entity Type
Business
Look and feel
Each slider illustrates characteristics of the customer's brand and the style your logo design should communicate.

```html
<!DOCTYPE html>
<html lang="en">
<head>
<meta charset="utf-8">
<title>Vantorin Kitchens – Business Cards</title>
<link rel="stylesheet" href="https://fonts.googleapis.com/css2?family=Arimo:wght@400;700&display=swap">
<style>
  :root {
    --stage: #9c7552;
    --card-top: #2b2b2d;
    --card-bottom: #0f0f10;
    --card-black: #050505;
    --silver-light: #d9d9db;
    --silver-mid: #a9a9ad;
    --silver-dark: #7d7d82;
    --accent-red: #d31a1a;
    --text-light: #f2f2f2;
    --text-dark-band: #ffffff;
    --label: #1d140c;
  }
  * { box-sizing: border-box; margin: 0; padding: 0; }
  html, body { width: 1200px; height: 788px; overflow: hidden; }
  body {
    position: relative;
    background: var(--stage);
    font-family: "Arimo", Arial, sans-serif;
  }
  .view-label {
    position: absolute;
    width: 300px;
    text-align: center;
    font-size: 21px;
    color: var(--label);
  }
  .card {
    position: absolute;
    width: 525px;
    height: 300px;
    border-radius: 22px;
    overflow: hidden;
    background: linear-gradient(180deg, var(--card-top), var(--card-bottom));
    box-shadow: 0 6px 14px rgba(0,0,0,0.45);
  }
  .card--black { background: var(--card-black); }

  .brand {
    position: absolute;
    left: 0; right: 0;
    display: flex;
    justify-content: center;
    align-items: center;
    gap: 12px;
  }
  .brand__square {
    width: 26px; height: 26px;
    background: var(--silver-mid);
  }
  .brand__name {
    font-weight: 700;
    font-size: 26px;
    letter-spacing: 1px;
    text-transform: uppercase;
    color: var(--silver-light);
  }
  .brand--large .brand__square { width: 34px; height: 34px; }
  .brand--large .brand__name { font-size: 33px; }

  .name-band {
    position: absolute;
    left: 0; right: 0;
    top: 148px;
    height: 76px;
    border-top: 2px solid var(--accent-red);
    border-bottom: 2px solid var(--accent-red);
    padding: 3px 0;
    background: var(--card-bottom);
  }
  .name-band__fill {
    height: 100%;
    background: linear-gradient(90deg, var(--silver-dark), var(--silver-mid) 55%, var(--silver-dark));
    position: relative;
  }
  .person {
    position: absolute;
    left: 45px; top: 9px;
    color: var(--text-dark-band);
  }
  .person__name { font-size: 19px; letter-spacing: 0.3px; }
  .person__title { font-size: 14px; margin-top: 2px; }
  .phones {
    position: absolute;
    right: 45px; top: 12px;
    text-align: right;
    font-size: 14px;
    line-height: 20px;
    color: var(--text-dark-band);
  }
  .card-footer {
    position: absolute;
    left: 0; right: 0;
    top: 241px;
    text-align: center;
    font-size: 13.5px;
    line-height: 19px;
    color: var(--text-light);
  }
  .sep { margin: 0 6px; }

  .texture {
    position: absolute;
  }
  .texture--top {
    left: 0; top: 0; width: 300px; height: 90px;
    background: radial-gradient(ellipse at 45% 20%, #4a4a4c, rgba(5,5,5,0) 70%);
  }
  .texture--bottom {
    right: 0; bottom: 0; width: 260px; height: 85px;
    background: radial-gradient(ellipse at 45% 70%, #4a4a4c, rgba(5,5,5,0) 70%);
  }
</style>
</head>
<body>
  <div class="view-label" style="left:157px; top:22px;">front</div>
  <div class="view-label" style="left:738px; top:22px;">front-1</div>
  <div class="view-label" style="left:164px; top:405px;">back</div>
  <div class="view-label" style="left:738px; top:405px;">Back - 1</div>

  <!-- Front: President -->
  <div class="card" style="left:50px; top:70px;">
    <div class="brand" style="top:88px;">
      <span class="brand__square"></span>
      <span class="brand__name">Vantorin Kitchens</span>
    </div>
    <div class="name-band">
      <div class="name-band__fill">
        <div class="person">
          <div class="person__name">MAREK DOVAN</div>
          <div class="person__title">President</div>
        </div>
        <div class="phones">
          <div><b>phone</b> : 555.214.0371</div>
          <div><b>cell</b> : 555.862.4410</div>
        </div>
      </div>
    </div>
    <div class="card-footer">
      <div><b>fax</b> : 555.214.0388<span class="sep">|</span><b>email</b> : marek@vantorinkitchens.ca</div>
      <div>1820 - 47 Ave., Larkfield, AB T4R 2M9</div>
    </div>
  </div>

  <!-- Front: Director -->
  <div class="card card--black" style="left:628px; top:70px;">
    <div class="brand" style="top:88px;">
      <span class="brand__square"></span>
      <span class="brand__name">Vantorin Kitchens</span>
    </div>
    <div class="name-band">
      <div class="name-band__fill">
        <div class="person">
          <div class="person__name">TOBIAS DOVAN</div>
          <div class="person__title">Director</div>
        </div>
        <div class="phones">
          <div><b>phone</b> : 555.214.0371</div>
          <div><b>cell</b> : 555.930.2265</div>
        </div>
      </div>
    </div>
    <div class="card-footer">
      <div><b>fax</b> : 555.214.0388<span class="sep">|</span><b>email</b> : tobias@vantorinkitchens.ca</div>
      <div>1820 - 47 Ave., Larkfield, AB T4R 2M9</div>
    </div>
  </div>

  <!-- Back -->
  <div class="card" style="left:56px; top:446px;">
    <div class="brand brand--large" style="top:130px;">
      <span class="brand__square"></span>
      <span class="brand__name">Vantorin Kitchens</span>
    </div>
  </div>

  <!-- Back alternative -->
  <div class="card card--black" style="left:624px; top:446px;">
    <div class="texture texture--top" role="img" aria-label="Perforated metal texture, top corner"></div>
    <div class="texture texture--bottom" role="img" aria-label="Perforated metal texture, bottom corner"></div>
    <div class="brand brand--large" style="top:145px;">
      <span class="brand__square"></span>
      <span class="brand__name">Vantorin Kitchens</span>
    </div>
  </div>
</body>
</html>
```